Kelvaro.ch is looking for business card letterhead and envelope C5 with WOW effect

We need a strong business card for our company Kelvaro.ch, logo is available. You want a black or dark background on which the logo Stark r% 26 # 252; appears. Letterhead and envelope in C5 format should be in a similar design, but does not have to be We need a strong business card for our company Kelvaro.ch, logo is available. A black or dark background is desired, on which the logo Stark comes across. The letterhead and the envelope in C5 format should have a similar design.

Target Market(s)

Private customers as well as entrepreneurs

Contact Information for Business Card

E-mail: info@kelvaro-example.ch
Web.www.Kelvaro-example.ch
Tel: +41 ( 0 ) 79 482 6037
Adresse:
Lindenweg 14
9406 Tarnbach

Hier kann man Icons verwenden für Email,Tel und Adressse

Font styles to use
Other font styles liked:
• Dubai,bold

Colors

Designer to choose colors to be used in the design.

Requirements
Must have
• WOW effect
Nice to have
• R% 26 # 252; back business card with our service listings. - VEHICLE LABELING - SHOP WINDOW LABELING - STICKERS AND MUCH MORE ... in red color

```html
<!DOCTYPE html>
<html lang="en">
<head>
<meta charset="utf-8">
<title>Kelvaro.ch – Business Card</title>
<link rel="stylesheet" href="https://fonts.googleapis.com/css2?family=Black+Ops+One&family=Ubuntu:wght@400;500;700&display=swap">
<style>
  :root {
    --stage: #2a2a2a;
    --card: #0b0b0b;
    --yellow: #fdc91c;
    --white: #ffffff;
    --faint: #161616;
  }
  * { margin: 0; padding: 0; box-sizing: border-box; }
  html, body { width: 1200px; height: 900px; overflow: hidden; }
  body {
    background: radial-gradient(circle at 60% 30%, #3a3a3a 0%, var(--stage) 45%, #121212 100%);
    font-family: "Ubuntu", sans-serif;
    position: relative;
  }
  .card {
    position: absolute;
    left: 250px;
    width: 700px;
    height: 400px;
    background: var(--card);
    overflow: hidden;
    box-shadow: 0 14px 30px rgba(0,0,0,.55);
  }
  .card--front { top: 35px; border-right: 5px solid var(--yellow); }
  .card--back  { top: 465px; border-left: 5px solid var(--yellow); }

  .front__pattern {
    position: absolute;
    left: 0; top: 0;
    width: 300px; height: 100%;
    background: linear-gradient(135deg, var(--card) 0%, #7a6110 35%, var(--yellow) 60%, #8d6f12 80%, var(--card) 100%);
  }
  .front__texture {
    position: absolute;
    right: 0; top: 0;
    width: 320px; height: 100%;
    background: radial-gradient(circle at 60% 55%, #1d1d1d 0%, var(--faint) 45%, var(--card) 80%);
  }
  .brand-name {
    font-family: "Ubuntu", sans-serif;
    font-weight: 700;
    color: var(--white);
    text-transform: uppercase;
    letter-spacing: 2px;
    white-space: nowrap;
  }
  .front__brand {
    position: absolute;
    left: 340px; top: 165px;
    font-size: 52px;
  }

  .back__brand {
    position: absolute;
    left: 55px; top: 168px;
    font-size: 40px;
  }
  .back__divider {
    position: absolute;
    left: 375px; top: 120px;
    width: 2px; height: 160px;
    background: var(--yellow);
  }
  .contact {
    position: absolute;
    left: 400px; top: 118px;
  }
  .contact__name {
    font-family: "Black Ops One", sans-serif;
    color: var(--yellow);
    font-size: 28px;
    letter-spacing: 2px;
    text-transform: uppercase;
    line-height: 1;
  }
  .contact__role {
    color: var(--white);
    font-size: 17px;
    margin: 4px 0 10px;
  }
  .contact__list { list-style: none; }
  .contact__item {
    display: flex;
    align-items: center;
    gap: 9px;
    color: var(--white);
    font-size: 16px;
    line-height: 27px;
  }
  .contact__icon { width: 17px; height: 17px; flex: none; }
  .contact__highlight { color: var(--yellow); font-weight: 700; }
</style>
</head>
<body>

<section class="card card--front">
  <div class="front__pattern" role="img" aria-label="Yellow honeycomb pattern of hexagons and outlined hexagons"></div>
  <div class="front__texture" role="img" aria-label="Faint dark honeycomb texture"></div>
  <div class="brand-name front__brand">Kelvaro.ch</div>
</section>

<section class="card card--back">
  <div class="brand-name back__brand">Kelvaro.ch</div>
  <div class="back__divider"></div>
  <div class="contact">
    <h1 class="contact__name">Marek Dorn</h1>
    <p class="contact__role">Owner/ CEO</p>
    <ul class="contact__list">
      <li class="contact__item">
        <svg class="contact__icon" viewBox="0 0 24 24" fill="none" stroke="#fdc91c" stroke-width="2"><circle cx="12" cy="12" r="10"/><path d="M8 7l2 0 1 3-1.5 1a6 6 0 003 3l1-1.5 3 1v2a2 2 0 01-2 2A9 9 0 016 9a2 2 0 012-2z"/></svg>
        +41 ( 0 ) 79 482 6037
      </li>
      <li class="contact__item">
        <svg class="contact__icon" viewBox="0 0 24 24" fill="none" stroke="#fdc91c" stroke-width="2"><rect x="2" y="5" width="20" height="14"/><path d="M2 5l10 8 10-8"/></svg>
        info@kelvaro-example.ch
      </li>
      <li class="contact__item">
        <svg class="contact__icon" viewBox="0 0 24 24" fill="none" stroke="#fdc91c" stroke-width="2"><circle cx="12" cy="12" r="10"/><path d="M2 12h20M12 2c3 3 3 17 0 20M12 2c-3 3-3 17 0 20"/></svg>
        <span>www.<span class="contact__highlight">Kelvaro-example</span>.ch</span>
      </li>
      <li class="contact__item">
        <svg class="contact__icon" viewBox="0 0 24 24" fill="none" stroke="#fdc91c" stroke-width="2"><path d="M3 11l9-8 9 8v10H3z"/><path d="M10 21v-6h4v6"/></svg>
        Lindenweg 14, 9406 Tarnbach
      </li>
    </ul>
  </div>
</section>

</body>
</html>
```